Website for my photography business

I need a website for my photography business, Bram Kellet Photography. I need a website that has a landing page with a cover photo of each kind of photography I do. For example, Nature, Weddings, Portraits and Architecture. I want it so that when someone comes onto my website they have to choose which kind of photography page they want to visit. So if they click on the wedding photo it will open to a page with my wedding portfolio images and a contact me button. If they choose nature photography I want them to be redirected to an e-commerce section where they can purchase prints. Architecture and Portraits should open up to their respective portfolios with about me and contact info. I like this kind of format because I want people who come to my website for a specific type of photography to be able to be directed there easily without having to look at a mix of other kinds of photography. I will provide a few files to use as placeholders. I have already purchased the bramkelletphotography.example domain name. A Wix website would be great because I am most familiar with it but I am open to anything.

Industry/Entity Type

Photographer

Number of Pages Required

5+ page

Requirements
Must have
• Landing Page and e-commerce

```html
<!DOCTYPE html>
<html lang="en">
<head>
<meta charset="utf-8">
<title>Bram Kellet Photography</title>
<link rel="stylesheet" href="https://fonts.googleapis.com/css2?family=Poppins:wght@400;500;600;700&family=Pinyon+Script&display=swap">
<style>
  :root {
    --purple: #2e2558;
    --navy: #1b3e5e;
    --navy-active: #1d3f60;
    --ink: #222222;
    --muted: #555555;
    --bar: #f2f2f2;
    --white: #ffffff;
  }
  * { box-sizing: border-box; margin: 0; padding: 0; }
  html, body { width: 700px; height: 1200px; overflow: hidden; }
  body { position: relative; background: var(--white); font-family: "Poppins", sans-serif; color: var(--ink); }
  .abs { position: absolute; }

  .topbar { left: 0; top: 0; width: 700px; height: 19px; background: var(--bar); border-bottom: 1px solid #dcdcdc;
    font-size: 7.5px; color: var(--muted); text-align: center; line-height: 18px; }

  .brand { left: 65px; top: 34px; font-family: "Poppins", sans-serif; font-size: 15px; font-weight: 500; color: var(--purple); }
  .social-top { top: 38px; display: flex; gap: 2px; left: 390px; }
  .social-top span { width: 22px; height: 22px; border: 1.5px solid var(--ink); border-radius: 50%; display: block; }
  .call { left: 508px; top: 36px; width: 127px; height: 25px; border-radius: 13px; background: var(--navy);
    color: var(--white); font-size: 10px; font-weight: 600; text-align: center; line-height: 25px; }

  .nav { left: 0; top: 77px; width: 700px; height: 23px; background: var(--purple); }
  .nav ul { list-style: none; display: flex; position: absolute; left: 71px; top: 0; height: 23px; }
  .nav li { color: var(--white); font-size: 8.5px; line-height: 23px; padding: 0 10px; }
  .nav li.active { background: var(--navy-active); padding: 0 13px; }

  .hero { left: 0; top: 100px; width: 700px; height: 316px;
    background: linear-gradient(100deg, #4a3a18 0%, #8a6a22 22%, #c07a24 40%, #9c5a20 55%, #2c3f9a 72%, #2338a8 100%); }
  .hero-glow { left: 0; top: 100px; width: 700px; height: 316px;
    background: linear-gradient(180deg, rgba(230,150,40,0.35) 0%, rgba(0,0,0,0) 45%, rgba(60,120,30,0.3) 100%); }
  .hero-panel { left: 201px; top: 187px; width: 354px; height: 143px; background: rgba(30,40,70,0.45); }
  .hero-title { left: 201px; top: 190px; width: 354px; text-align: center; font-family: "Pinyon Script", cursive;
    font-size: 29px; color: var(--white); }
  .hero-text { left: 201px; top: 238px; width: 354px; text-align: center; font-size: 10px; font-weight: 500;
    line-height: 16px; color: var(--white); }
  .hero-btn { left: 298px; top: 288px; width: 104px; height: 28px; border-radius: 14px; background: var(--navy);
    color: var(--white); font-size: 9.5px; font-weight: 600; text-align: center; line-height: 28px; }
  .arrow { top: 246px; width: 25px; height: 25px; }

  .section-title { left: 0; top: 458px; width: 700px; text-align: center; font-family: "Pinyon Script", cursive;
    font-size: 27px; color: var(--purple); }

  .card { overflow: hidden; }
  .card .shade { position: absolute; inset: 0; background: linear-gradient(180deg, rgba(0,0,0,0) 40%, rgba(0,0,0,0.35) 100%); }
  .card h3 { position: absolute; font-size: 16px; font-weight: 700; color: var(--white); }
  .card p { position: absolute; font-size: 8px; color: var(--white); }
  .card .btn { position: absolute; height: 26px; border-radius: 13px; background: var(--navy); color: var(--white);
    font-size: 8.5px; font-weight: 600; text-align: center; line-height: 26px; }

  .footer { left: 0; top: 971px; width: 700px; height: 229px; background: var(--purple); color: var(--white); }
  .footer h4 { position: absolute; top: 57px; font-size: 9.5px; font-weight: 500; }
  .footer ul { position: absolute; list-style: none; top: 77px; font-size: 7.5px; }
  .footer ul li { height: 15.5px; }
  .contact-list li { display: flex; gap: 8px; height: 17px; }
  .contact-list svg { flex: none; margin-top: 1px; }
  .email-input { left: 479px; top: 80px; width: 155px; height: 22px; border-radius: 11px; background: var(--white);
    color: var(--muted); font-size: 8px; line-height: 22px; padding-left: 10px; }
  .submit { left: 480px; top: 110px; width: 89px; height: 21px; border-radius: 11px; background: var(--navy);
    font-size: 8.5px; font-weight: 600; text-align: center; line-height: 21px; }
  .social-foot { left: 490px; top: 145px; display: flex; gap: 3px; }
  .social-foot span { width: 22px; height: 22px; border-radius: 50%; background: var(--white); display: block; }
  .rule { left: 65px; top: 188px; width: 570px; height: 1px; background: rgba(255,255,255,0.15); }
  .copyright { left: 0; top: 201px; width: 700px; text-align: center; font-size: 8px; }
</style>
</head>
<body>
  <div class="abs topbar">Lorem ipsum dolor sit amet, consectetur adipiscing elit,</div>

  <header>
    <div class="abs brand">Bram Kellet Photography</div>
    <div class="abs social-top" aria-label="Social links"><span></span><span></span><span></span><span></span></div>
    <div class="abs call">Call Us: 123-456-789</div>
  </header>

  <nav class="abs nav">
    <ul>
      <li class="active">Home</li><li>About Me</li><li>Nature</li><li>Weddings</li><li>Potraits</li>
      <li>Architecture</li><li>Shop</li><li>portfolio</li><li>News</li><li>Contact Us</li>
    </ul>
  </nav>

  <section>
    <div class="abs hero" role="img" aria-label="Autumn trees with orange leaves beside a blue lake"></div>
    <div class="abs hero-glow"></div>
    <div class="abs hero-panel"></div>
    <div class="abs hero-title">Bram Kellet Photography</div>
    <div class="abs hero-text">Lorem ipsum dolor sit amet, consectetur adipiscing<br>elit, sed do eiusmod tempor incididunt</div>
    <div class="abs hero-btn">GET STARTED</div>
    <svg class="abs arrow" style="left:19px" viewBox="0 0 25 25"><circle cx="12.5" cy="12.5" r="11.5" fill="none" stroke="#fff" stroke-width="1.2"/><path d="M14 8 L10 12.5 L14 17" fill="none" stroke="#fff" stroke-width="1.3"/></svg>
    <svg class="abs arrow" style="left:658px" viewBox="0 0 25 25"><circle cx="12.5" cy="12.5" r="11.5" fill="none" stroke="#fff" stroke-width="1.2"/><path d="M11 8 L15 12.5 L11 17" fill="none" stroke="#fff" stroke-width="1.3"/></svg>
  </section>

  <section>
    <h2 class="abs section-title">Our Work</h2>

    <div class="abs card" style="left:72px;top:517px;width:325px;height:189px;background:linear-gradient(135deg,#8a7a68,#b09478 45%,#6d5e50);" role="img" aria-label="Dark wedding ring resting on a speckled stone">
      <div class="shade"></div>
      <h3 style="left:29px;top:99px">Weddings</h3>
      <p style="left:29px;top:123px">Lorem ipsum dolor sit amet, consectetur elit,</p>
      <div class="btn" style="left:30px;top:146px;width:88px">CONTACT ME</div>
    </div>

    <div class="abs card" style="left:414px;top:517px;width:214px;height:189px;background:linear-gradient(160deg,#2d3a26,#5a4a30 45%,#c8ccd2 100%);" role="img" aria-label="Red fox sitting in a snowy pine forest">
      <div class="shade"></div>
      <h3 style="left:18px;top:99px">Nature</h3>
      <p style="left:19px;top:123px">Lorem ipsum dolor sit amet, elit,</p>
      <div class="btn" style="left:20px;top:146px;width:93px">PURCHASE PRINTS</div>
    </div>

    <div class="abs card" style="left:72px;top:722px;width:214px;height:189px;background:linear-gradient(135deg,#d0d0d0,#7a7a7a 50%,#2a2a2a);" role="img" aria-label="Black and white close-up portrait study">
      <div class="shade"></div>
      <h3 style="left:18px;top:99px">Portraits</h3>
      <p style="left:19px;top:123px">Lorem ipsum dolor sit amet, elit,</p>
      <div class="btn" style="left:20px;top:146px;width:94px">ABOUT ME</div>
    </div>

    <div class="abs card" style="left:303px;top:722px;width:325px;height:189px;background:linear-gradient(180deg,#c9cdd2 0%,#9a6a52 40%,#6e5444 75%,#4e5a3a 100%);" role="img" aria-label="Modern brick and stone building with glass balconies">
      <div class="shade"></div>
      <h3 style="left:29px;top:99px">Architecture</h3>
      <p style="left:29px;top:123px">Lorem ipsum dolor sit amet, consectetur elit,</p>
      <div class="btn" style="left:29px;top:146px;width:89px">CONTACT INFO</div>
    </div>
  </section>

  <footer class="abs footer">
    <h4 style="left:65px">CONTACT INFO</h4>
    <ul class="contact-list" style="left:66px;top:77px">
      <li><svg width="8" height="8" viewBox="0 0 8 8"><path d="M1 3 Q4 0 7 3 L6 4 L5 3 L3 3 L2 4 Z M2 4 H6 V7 H2 Z" fill="#fff"/></svg>(888) 888-8888</li>
      <li><svg width="8" height="8" viewBox="0 0 8 8"><rect x="2" y="0.5" width="4" height="2" fill="#fff"/><rect x="0.5" y="3" width="7" height="3" fill="#fff"/><rect x="2" y="5" width="4" height="2.5" fill="#fff"/></svg>(888) 888-888</li>
      <li><svg width="8" height="8" viewBox="0 0 8 8"><rect x="0.5" y="1.5" width="7" height="5" fill="none" stroke="#fff"/><path d="M0.5 1.5 L4 4.5 L7.5 1.5" fill="none" stroke="#fff"/></svg><span style="text-decoration:underline">info@bramkellet.example</span></li>
      <li style="height:auto"><svg width="8" height="9" viewBox="0 0 8 9"><path d="M4 8.5 C1 5 1 4 1 3.2 A3 3 0 0 1 7 3.2 C7 4 7 5 4 8.5 Z" fill="#fff"/><circle cx="4" cy="3.2" r="1" fill="#2e2558"/></svg><span style="line-height:8.5px">#2868 Lorem ipsum dolor<br>sit amet, consectetur</span></li>
    </ul>

    <h4 style="left:217px">QUICK LINKS</h4>
    <ul style="left:217px"><li>Home</li><li>About</li><li>Professional Gamer</li><li>Reviews</li><li>Gallery</li></ul>

    <h4 style="left:350px">INFORMATION</h4>
    <ul style="left:350px"><li>Terms &amp; Conditions</li><li>Privacy Policy</li><li>Disclaimer</li><li>Site Map</li><li>Contact Us</li></ul>

    <h4 style="left:478px;top:58px">NEWSLETTER SUBSCRIPTION</h4>
    <div class="abs email-input">Enter your email</div>
    <div class="abs submit">SUBMIT</div>
    <div class="abs social-foot" aria-label="Social links"><span></span><span></span><span></span><span></span></div>

    <div class="abs rule"></div>
    <div class="abs copyright">© Copyright 2020 Bram Kellet Photography, All Rights Reserved</div>
  </footer>
</body>
</html>
```